Pharmacy In Bahamas Needs Teacher Appreciation Advertisement

We need an advertisement design for a small pharmacy in the Bahamas. This ad is to attract elementary students to vote on friendloop and in store for their favorite teacher. The teacher with the most votes wins a $300 store credit and school supplies for his/her class. The campaign will be printed in store on 5.5" x 8.5 sized prints, and posted online. All submissions should be double-sided. Any images of school children should be uniformed.

Target Market(s)

Elementary School Students, Parents of Elementary School Students, Elementary School Teachers,

Industry/Entity Type

Pharmacy

Font styles to use
Sans Serif

Colors
acd036
ec2027
ffffff
33a6d7

Requirements
Must have
• "Follow Us on Friendloop" Icon "Follow Us on Quipline"
• www.coralgatedrugmart.com
Nice to have
• Simplistic clean design, if images of people are used it should be diverse,
Should not have
• Too much white space, too much text or look similar to existing ad (see attached, but please use text of existing.

```html
<!DOCTYPE html>
<html lang="en">
<head>
<meta charset="utf-8">
<title>Coral Gate Drug Mart – Teachers Appreciation Competition</title>
<link rel="stylesheet" href="https://fonts.googleapis.com/css2?family=Arvo:wght@400;700&family=Alegreya:wght@400;700&display=swap">
<style>
  :root{
    --green:#acd036;
    --red:#ec2027;
    --white:#ffffff;
    --blue:#33a6d7;
    --ink:#3a3a3a;
    --backdrop:#e8e4dd;
    --leaf:#2f8f3a;
  }
  *{margin:0;padding:0;box-sizing:border-box}
  html,body{width:1200px;height:1000px;overflow:hidden;background:var(--backdrop)}
  .flyer{position:absolute;left:330px;top:75px;width:540px;height:850px;background:var(--white);overflow:hidden;font-family:"Alegreya",Georgia,serif;color:var(--ink)}
  .flyer-shapes{position:absolute;inset:0;width:540px;height:850px}
  .block{position:absolute;left:0;width:540px;text-align:center}
  .brand{top:38px;display:flex;align-items:center;justify-content:center;gap:12px}
  .brand-dot{width:34px;height:34px;border-radius:50%;background:var(--red)}
  .brand-name{font-family:"Arvo",Georgia,serif;font-weight:700;font-size:25px;color:var(--red);letter-spacing:.5px}
  .brand-tagline{top:86px;font-size:14px;color:var(--leaf)}
  .headline{top:168px;font-family:"Arvo",Georgia,serif;font-weight:700;font-size:74px;color:var(--white);line-height:1}
  .subhead{top:292px;font-family:"Arvo",Georgia,serif;font-weight:700;font-size:26px;line-height:32px;color:var(--red)}
  .week{top:352px;font-family:"Arvo",Georgia,serif;font-weight:700;font-size:19px;color:var(--blue)}
  .nominate{top:393px;font-size:14px}
  .prize{top:425px;font-size:18px;line-height:22px}
  .prize .amount{color:var(--red)}
  .vote{top:505px;font-size:17px;color:var(--blue)}
  .kids-art{position:absolute;left:75px;top:540px;width:400px;height:150px;border-radius:10px;background:linear-gradient(180deg,#f6e3b8 0%,#f3d9b0 55%,#fbf8f2 100%)}
  .follow{top:722px;display:flex;align-items:center;justify-content:center;gap:14px}
  .social{display:flex;align-items:center;gap:6px;font-family:"Arvo",Georgia,serif;font-weight:700;font-size:13px;color:var(--white)}
  .social-dot{width:42px;height:42px;border-radius:50%;background:var(--blue);border:2px solid var(--white)}
  .follow-title{font-family:"Arvo",Georgia,serif;font-weight:700;font-size:34px;color:var(--white)}
  .hours{top:776px;font-size:11px;color:var(--white)}
  .website{top:808px;font-family:"Arvo",Georgia,serif;font-weight:700;font-size:22px;color:var(--green)}
</style>
</head>
<body>
<main class="flyer">
  <svg class="flyer-shapes" viewBox="0 0 540 850" aria-hidden="true">
    <path d="M0 150 Q270 112 540 128 L540 280 Q270 292 0 286 Z" fill="var(--red)"/>
    <path d="M0 362 Q270 330 540 338" fill="none" stroke="var(--green)" stroke-width="4"/>
    <path d="M0 648 Q270 725 540 640 L540 800 L0 800 Z" fill="var(--green)"/>
  </svg>

  <header>
    <div class="block brand"><span class="brand-dot"></span><span class="brand-name">Coral Gate Drug Mart</span></div>
    <p class="block brand-tagline">Healthier choices, <b>Lower</b> Prices</p>
  </header>

  <h1 class="block headline">Teachers</h1>
  <h2 class="block subhead">Appreciation Competition</h2>

  <p class="block week">May 5 - 9 is Teachers Appreciation Week.</p>
  <p class="block nominate">Nominate one teacher to enter our theacher appreciation competition.</p>
  <p class="block prize">The teacher with the most votes wins a <span class="amount">$300</span> store credit,<br>supplies for the class and bragging rights as<br>the most popular teacher of the year!!!</p>
  <p class="block vote">Any purchase qualifies yu to vote for your favorite teacher.</p>

  <div class="kids-art" role="img" aria-label="Illustration of smiling school children holding a banner reading most popular teacher of the year, with a balloon and flowers on grass"></div>

  <footer>
    <div class="block follow">
      <span class="social"><span class="social-dot"></span>Friendloop</span>
      <span class="follow-title">Follow us</span>
      <span class="social">Quipline<span class="social-dot"></span></span>
    </div>
    <p class="block hours">Seabreeze Plaza&nbsp; / &nbsp;Open: Mon - Sat&nbsp; 8:00 a.m - 8:00 p.m; Sunday 8:00 a.m - 3:00 a.m</p>
    <p class="block website">www.coralgatedrugmart.com</p>
  </footer>
</main>
</body>
</html>
```